Form With Marla - Health and Wellness Business Card and Logo

I need a business card design with a logo for my business you can check out at www.formwithmarla.net. I want something more original, simplistic, and memorable than the basic logo I have on my site currently. I am a health and wellness coach and I offer mindset coaching and nutrition plans. I like the colour teal and dark grey/black for my theme colours. I emphasize growth, longterm change, and the whole package of "healthy mind, healthy body, healthy life". I had played around the idea of intertwining 3 M's or incorporating growth (leaves etc.) into my design. I want my expertise and experience to show through. In one glance I want people to understand with confidence I can help them accomplish anything they set their minds to. I look forward to seeing what everyone comes up with!

Industry/Entity Type

Health And Wellness

Contact Information for Business Card

Form With Marla
Marla Prentiss
BSc, Health & Wellness Coach
"Manifest your best"
www.formwithmarla.net
formwithmarla@quillpost.net
472-618-9043

Colors
33b8a4
ffffff
333333
000000

Requirements
Must have
• A memorable and unique logo for my business!
Nice to have
• Could have the phrase "Are you unhappy with your body and state of health?" or "It takes the right skills to develop habits in order to create long term change. I can help you get there."

```html
<!DOCTYPE html>
<html lang="en">
<head>
<meta charset="utf-8">
<title>Form With Marla – Business Card</title>
<link rel="stylesheet" href="https://fonts.googleapis.com/css2?family=Questrial&family=Open+Sans:wght@400;700&display=swap">
<style>
  :root {
    --stage: #2b2b2b;
    --card-dark: #1f1f1f;
    --card-dark-edge: #2a2a2a;
    --mark-grey: #8a8a8a;
    --rule-grey: #6b6b6b;
    --teal-light: #129e9b;
    --teal: #0a8a87;
    --teal-deep: #057774;
    --white: #ffffff;
  }
  * { box-sizing: border-box; margin: 0; padding: 0; }
  html, body {
    width: 1200px; height: 1000px; overflow: hidden;
    background: var(--stage);
  }
  .canvas {
    position: relative; width: 1200px; height: 1000px;
  }
  .card {
    position: absolute; left: 220px; width: 760px; height: 434px;
    border-radius: 4px; overflow: hidden;
  }

  /* Front: dark */
  .card-front {
    top: 50px;
    background: linear-gradient(160deg, var(--card-dark-edge), var(--card-dark));
  }
  .front-mark {
    position: absolute; left: 0; right: 0; top: 120px;
    display: flex; flex-direction: column; align-items: center;
  }
  .front-mark .mark-row {
    display: flex; align-items: center; gap: 14px;
  }
  .front-mark .mark-square {
    width: 30px; height: 30px; background: var(--mark-grey);
  }
  .front-mark .mark-name {
    font-family: "Questrial", sans-serif; font-size: 40px;
    color: var(--mark-grey); letter-spacing: 0.5px;
  }
  .front-mark .mark-rule {
    width: 270px; height: 1px; background: var(--rule-grey); margin-top: 10px;
  }
  .tagline {
    position: absolute; left: 0; right: 0; bottom: 62px;
    text-align: center; font-family: "Open Sans", sans-serif;
    font-size: 16px; letter-spacing: 5px; color: var(--white);
  }

  /* Back: teal */
  .card-back {
    top: 520px;
    background: radial-gradient(ellipse at 55% 55%, var(--teal-light) 0%, var(--teal) 45%, var(--teal-deep) 100%);
    color: var(--white);
  }
  .brand-title {
    position: absolute; left: 44px; top: 30px;
    font-family: "Questrial", sans-serif; font-size: 46px; font-weight: 400;
  }
  .name-tab {
    position: absolute; left: 0; top: 128px; width: 12px; height: 34px;
    background: var(--white); border-radius: 0 4px 4px 0;
  }
  .person-name {
    position: absolute; left: 44px; top: 122px;
    font-family: "Open Sans", sans-serif; font-weight: 700; font-size: 28px;
    letter-spacing: 0.5px;
  }
  .person-role {
    position: absolute; left: 44px; top: 160px;
    font-family: "Open Sans", sans-serif; font-weight: 700; font-size: 15px;
  }
  .contact-list {
    position: absolute; left: 40px; top: 220px; list-style: none;
    font-family: "Open Sans", sans-serif; font-size: 19px;
  }
  .contact-list li {
    display: flex; align-items: center; gap: 14px; height: 30px;
  }
  .contact-list svg { width: 16px; height: 16px; flex: none; }
  .contact-list .strong { font-weight: 700; }
  .back-mark {
    position: absolute; right: 40px; bottom: 40px;
    display: flex; align-items: center; gap: 10px;
  }
  .back-mark .mark-square { width: 22px; height: 22px; background: var(--white); }
  .back-mark .mark-name {
    font-family: "Questrial", sans-serif; font-size: 24px; color: var(--white);
  }
</style>
</head>
<body>
<main class="canvas">

  <section class="card card-front" aria-label="Card front">
    <div class="front-mark">
      <div class="mark-row">
        <span class="mark-square"></span>
        <span class="mark-name">Form With Marla</span>
      </div>
      <span class="mark-rule"></span>
    </div>
    <p class="tagline">"Manifest your best"</p>
  </section>

  <section class="card card-back" aria-label="Card back">
    <h1 class="brand-title">Form With Marla</h1>
    <span class="name-tab"></span>
    <h2 class="person-name">MARLA PRENTISS</h2>
    <p class="person-role">BSc, Health &amp; Wellness Coach</p>

    <ul class="contact-list">
      <li>
        <svg viewBox="0 0 16 16" aria-hidden="true"><path fill="#fff" d="M3.5 1.5l2.3 0 1 3.2-1.5 1.2c.9 1.9 2.4 3.4 4.3 4.3l1.2-1.5 3.2 1v2.3c0 .8-.7 1.5-1.5 1.5C6.7 13.5 2 8.8 2 3c0-.8.7-1.5 1.5-1.5z"/></svg>
        <span>472-618-9043</span>
      </li>
      <li>
        <svg viewBox="0 0 16 16" aria-hidden="true"><rect x="1" y="3" width="14" height="10" fill="#fff"/><path d="M1 3l7 5.5L15 3" fill="none" stroke="#0a8a87" stroke-width="1.4"/></svg>
        <span>formwithmarla@quillpost.net</span>
      </li>
      <li>
        <svg viewBox="0 0 16 16" aria-hidden="true"><g fill="none" stroke="#fff" stroke-width="1.3"><circle cx="8" cy="8" r="6.5"/><ellipse cx="8" cy="8" rx="3" ry="6.5"/><path d="M1.5 8h13M2.5 4.8h11M2.5 11.2h11"/></g></svg>
        <span>www.<span class="strong">formwithmarla</span>.net</span>
      </li>
      <li>
        <svg viewBox="0 0 16 16" aria-hidden="true"><circle cx="8" cy="8" r="6" fill="none" stroke="#fff" stroke-width="1.6"/></svg>
        <span>@marlaprentiss</span>
      </li>
    </ul>

    <div class="back-mark">
      <span class="mark-square"></span>
      <span class="mark-name">Form With Marla</span>
    </div>
  </section>

</main>
</body>
</html>
```